design a construction company business card

Design business card around our logo. Card must have all the typical info: name, title, address, phone, email, business name, etc. Somewhere on the card I would like to see our motto "Built on integrity... Inspired by commitment." Consider adding a splash of bright orange to the card to complement the blues and silvers/grays in the logo. We are open to metallic inks, textures, etc. We would like to see options on both light and dark backgrounds. The font in the logo is Euro Technic Extended Regular.

```html
<!DOCTYPE html>
<html lang="en">
<head>
<meta charset="utf-8">
<title>Halden Contracting – Business Card</title>
<link href="https://fonts.googleapis.com/css2?family=Roboto:wght@300;400;500&display=swap" rel="stylesheet">
<style>
  :root {
    --backdrop: #1a1a1a;
    --card: #0b0b0b;
    --card-edge: #222222;
    --silver: #e6e6e6;
    --silver-muted: #9a9a9a;
    --silver-dim: #4a4a4a;
  }
  * { margin: 0; padding: 0; box-sizing: border-box; }
  html, body {
    width: 1200px; height: 913px; overflow: hidden;
    background: var(--backdrop);
    font-family: "Roboto", Arial, sans-serif;
  }
  .canvas { position: relative; width: 1200px; height: 913px; }
  .card {
    position: absolute; width: 560px; height: 320px;
    background: var(--card);
    border: 1px solid var(--card-edge);
    box-shadow: 0 20px 40px rgba(0,0,0,.5);
    overflow: hidden;
  }
  .card--front { left: 80px; top: 110px; }
  .card--back { left: 560px; top: 480px; }

  .front-brand {
    position: absolute; left: 0; right: 0; top: 112px;
    display: flex; justify-content: center; align-items: center; gap: 14px;
  }
  .brand-square { width: 16px; height: 16px; background: var(--silver); flex: none; }
  .brand-name {
    font-weight: 400; font-size: 40px; letter-spacing: 6px;
    color: var(--silver); text-transform: uppercase;
  }
  .motto {
    position: absolute; left: 0; right: 0; top: 190px;
    text-align: center; font-weight: 300; font-size: 15px;
    letter-spacing: .5px; color: var(--silver);
  }
  .motto .faint { color: var(--silver-dim); }

  .back-brand {
    position: absolute; left: 40px; top: 160px;
    display: flex; align-items: flex-start; gap: 10px;
  }
  .back-brand .brand-square { width: 10px; height: 10px; margin-top: 7px; }
  .back-brand .brand-name {
    font-size: 20px; letter-spacing: 1px; line-height: 1.25;
    display: block; width: 250px;
  }

  .contact {
    position: absolute; left: 330px; top: 70px; width: 200px;
    color: var(--silver); font-weight: 300; font-size: 13px; line-height: 1.35;
  }
  .contact-name { font-weight: 400; font-size: 19px; line-height: 1.1; }
  .contact-title { font-size: 14px; margin-bottom: 14px; }
  .contact-address { margin-bottom: 12px; }
</style>
</head>
<body>
<main class="canvas">
  <section class="card card--front" aria-label="Card front">
    <div class="front-brand">
      <span class="brand-square"></span>
      <span class="brand-name">Halden</span>
    </div>
    <p class="motto"><span class="faint">Built on integrity... </span>Inspired by commitment.</p>
  </section>

  <section class="card card--back" aria-label="Card back">
    <div class="back-brand">
      <span class="brand-square"></span>
      <span class="brand-name">Halden<br>Contracting, Inc.</span>
    </div>
    <div class="contact">
      <p class="contact-name">Marcus Reed</p>
      <p class="contact-title">President</p>
      <p class="contact-address">2291 Birchwood Court<br>Anchorage, Alaska 99508</p>
      <p class="contact-lines">555-318-7040<br>marcus@halden.com<br>www.halden.com</p>
    </div>
  </section>
</main>
</body>
</html>
```